Business Card Design for Software Development Company

I am looking for a business card design the incorporates my new logo (attached below).

Key information to include:
Name: Martin Quelbrook
Title: CEO
Email: martin@brightwellcivic.example
Phone: 555-218-9403
Website: www.brightwellcivic.example

NOTE: This design should be easy to edit so that we can order cards for different members of our team.

```html
<!DOCTYPE html>
<html lang="en">
<head>
<meta charset="utf-8">
<title>Brightwell Labs – Business Card</title>
<link rel="stylesheet" href="https://fonts.googleapis.com/css2?family=Montserrat:wght@400;600;700&display=swap">
<style>
  :root {
    --stage: #232323;
    --card-dark: #1d1d1d;
    --card-light: #ffffff;
    --ink: #222222;
    --ink-soft: #3a3a3a;
    --teal: #13b29c;
    --orange: #ec7f27;
    --peach: #f8c08a;
  }
  * { box-sizing: border-box; margin: 0; padding: 0; }
  html, body { width: 1200px; height: 900px; overflow: hidden; }
  body {
    background: var(--stage);
    font-family: "Montserrat", sans-serif;
    position: relative;
  }
  .card {
    position: absolute;
    left: 250px;
    width: 700px;
    height: 400px;
    overflow: hidden;
  }
  .card--back { top: 40px; background: var(--card-dark); }
  .card--front { top: 460px; background: var(--card-light); }

  .brand {
    display: flex;
    align-items: center;
    gap: 14px;
    font-weight: 700;
    letter-spacing: -0.5px;
    white-space: nowrap;
  }
  .brand__mark { width: 18px; height: 18px; background: var(--teal); flex: none; }
  .card--back .brand {
    position: absolute; left: 0; right: 0; top: 168px;
    justify-content: center;
    color: #ffffff; font-size: 52px; line-height: 64px;
  }
  .card--front .brand {
    position: absolute; left: 54px; top: 120px;
    color: var(--ink); font-size: 44px; line-height: 54px;
  }

  .accent-disc {
    position: absolute; left: 470px; top: 40px;
    width: 190px; height: 190px; border-radius: 50%;
    background: var(--orange);
  }

  .person { position: absolute; left: 56px; top: 205px; }
  .person__name {
    font-weight: 700; font-size: 25px; letter-spacing: 0.5px; line-height: 30px;
    text-transform: uppercase;
    white-space: nowrap;
  }
  .person__first { color: var(--teal); }
  .person__last { color: var(--orange); }
  .person__title { font-size: 17px; color: var(--ink-soft); margin-top: 2px; }
  .person__rule { width: 14px; height: 2px; background: var(--orange); margin: 10px 0 8px; }

  .contacts { list-style: none; }
  .contacts__item {
    display: flex; align-items: center; gap: 12px;
    font-size: 16px; color: var(--ink); line-height: 26px;
    white-space: nowrap;
  }
  .contacts__icon { width: 16px; height: 16px; flex: none; }

  .base-band {
    position: absolute; left: 0; bottom: 0;
    width: 700px; height: 16px;
    background: linear-gradient(90deg, var(--teal), var(--orange) 70%, var(--peach));
  }
</style>
</head>
<body>

<section class="card card--back" aria-label="Card back">
  <div class="brand"><span class="brand__mark"></span>Brightwell Labs</div>
</section>

<section class="card card--front" aria-label="Card front">
  <div class="accent-disc"></div>

  <div class="brand"><span class="brand__mark"></span>Brightwell Labs</div>

  <div class="person">
    <p class="person__name"><span class="person__first">Martin</span> <span class="person__last">Quelbrook</span></p>
    <p class="person__title">CEO</p>
    <div class="person__rule"></div>
    <ul class="contacts">
      <li class="contacts__item">
        <svg class="contacts__icon" viewBox="0 0 16 16" aria-hidden="true"><path d="M2 6c0-2 3-3 6-3s6 1 6 3v1h-3V5.5H5V7H2z M4 8h8l2 5H2z" fill="var(--peach)"/></svg>
        555-218-9403
      </li>
      <li class="contacts__item">
        <svg class="contacts__icon" viewBox="0 0 16 16" aria-hidden="true"><rect x="1" y="3" width="14" height="10" fill="var(--teal)"/><path d="M1 3l7 6 7-6" fill="none" stroke="#fff" stroke-width="1.4"/></svg>
        martin@brightwellcivic.example
      </li>
      <li class="contacts__item">
        <svg class="contacts__icon" viewBox="0 0 16 16" aria-hidden="true"><circle cx="8" cy="8" r="7" fill="var(--orange)"/><path d="M1 8h14M8 1c-3 3-3 11 0 14M8 1c3 3 3 11 0 14" fill="none" stroke="#fff" stroke-width="1.1"/></svg>
        www.brightwellcivic.example
      </li>
    </ul>
  </div>

  <div class="base-band" role="img" aria-label="Decorative colour band along the bottom edge, teal through orange to peach"></div>
</section>

</body>
</html>
```